One Thumbnail for Online Shop for PowerPoint Templates needed

We are selling PowerPoint Templates and need therefore a thumbnail for our online shop.

You can use a stock photo, mock-ups or other design elements.

Format:
squared like 500 x 500
or wide like 1280 x 720

If you want to use a title, use:

"Graphs" ---> Title
"PowerPoint template" ---> subtitle

Attachments:
- OLD: Our old thumbnail which I do not like
- Template: PowerPoint pictures which you can use ( you can also copy them if you need more than these)
- Example: Some examples I found from other shops (please do not copy them exactly, only to show what I mean)

I received lots of designs until now but many are not what I have expected

Target Market(s)

E-Commerce

Industry/Entity Type

Shop

Font styles to use
Sans Serif

Requirements
Should not have
• Do NOT re-design one of the template.png (these are only examples, I will replace them later)

```html
<!DOCTYPE html>
<html lang="en">
<head>
<meta charset="utf-8">
<title>Standard Graphs – Slide Deck Presentation</title>
<link rel="stylesheet" href="https://fonts.googleapis.com/css2?family=Orbitron:wght@400&family=Exo+2:wght@200;300&family=Arimo:wght@400;700&display=swap">
<style>
  :root {
    --bg-deep: #1d3444;
    --bg-mid: #3c5f6c;
    --bg-light: #9fb9a8;
    --slide-bg: #f7f9fb;
    --ink: #222b33;
    --muted: #6b7580;
    --navy: #1f3a5f;
    --blue: #4a90d9;
    --white: #ffffff;
  }
  * { margin: 0; padding: 0; box-sizing: border-box; }
  html, body { width: 1200px; height: 753px; overflow: hidden; }
  body { font-family: "Arimo", Arial, sans-serif; background: var(--bg-deep); }
  .thumbnail { position: relative; width: 1200px; height: 753px; overflow: hidden; }
  .backdrop-photo {
    position: absolute; inset: 0;
    background:
      radial-gradient(ellipse 420px 260px at 1080px 330px, rgba(200,215,225,0.55), transparent 70%),
      linear-gradient(180deg, var(--bg-light) 0%, #6f9189 22%, var(--bg-mid) 42%, #2c4a5a 65%, var(--bg-deep) 100%);
  }
  .slide {
    position: absolute; width: 304px; height: 171px;
    background: var(--slide-bg);
    box-shadow: 0 2px 8px rgba(0,0,0,0.25);
  }
  .slide svg { display: block; width: 100%; height: 100%; }
  .slide-one { left: 106px; top: 94px; }
  .slide-two { left: 106px; top: 304px; }
  .slide-three { left: 107px; top: 511px; }
  .s-title { font: 700 12px "Arimo", Arial, sans-serif; fill: var(--ink); }
  .s-sub { font: 400 6.6px "Arimo", Arial, sans-serif; fill: var(--ink); }
  .s-cap { font: 700 5.5px "Arimo", Arial, sans-serif; fill: var(--ink); }
  .s-tiny { font: 400 3.6px "Arimo", Arial, sans-serif; fill: var(--muted); }
  .s-lbl { font: 400 5px "Arimo", Arial, sans-serif; fill: var(--muted); }
  .s-val { font: 400 5px "Arimo", Arial, sans-serif; fill: var(--white); }
  .s-acc { font: 400 5px "Arimo", Arial, sans-serif; fill: var(--blue); }
  .headline {
    position: absolute; left: 470px; top: 466px;
    color: var(--white);
  }
  .headline-title {
    font-family: "Orbitron", "Exo 2", sans-serif;
    font-weight: 400; font-size: 70px; line-height: 80px; letter-spacing: 0;
  }
  .headline-sub {
    margin-top: 14px;
    font-family: "Exo 2", Arial, sans-serif;
    font-weight: 200; font-size: 45px; letter-spacing: 1.5px; line-height: 50px;
    white-space: nowrap;
  }
</style>
</head>
<body>
<div class="thumbnail">
  <div class="backdrop-photo" role="img" aria-label="Blurred photo of a desk with a keyboard and a laptop showing chart slides"></div>

  <div class="slide slide-one">
    <svg viewBox="0 0 380 214">
      <defs>
        <g id="mini-chart">
          <text class="s-cap" x="0" y="0">Lorem ipsum</text>
          <text class="s-tiny" x="0" y="6">Lorem ipsum dolor sit amet, consectetuer</text>
          <line x1="5" y1="62" x2="108" y2="62" stroke="#ccd" stroke-width="0.5"/>
          <g fill="var(--navy)">
            <rect x="8" y="44" width="5" height="18"/><rect x="16" y="42" width="5" height="20"/>
            <rect x="24" y="38" width="5" height="24"/><rect x="32" y="40" width="5" height="22"/>
            <rect x="40" y="41" width="5" height="21"/><rect x="48" y="43" width="5" height="19"/>
            <rect x="56" y="40" width="5" height="22"/><rect x="64" y="44" width="5" height="18"/>
            <rect x="72" y="42" width="5" height="20"/><rect x="80" y="45" width="5" height="17"/>
            <rect x="88" y="43" width="5" height="19"/><rect x="96" y="41" width="5" height="21"/>
          </g>
          <g fill="var(--blue)">
            <rect x="8" y="38" width="5" height="6"/><rect x="16" y="28" width="5" height="14"/>
            <rect x="24" y="20" width="5" height="18"/><rect x="32" y="26" width="5" height="14"/>
            <rect x="40" y="26" width="5" height="15"/><rect x="48" y="30" width="5" height="13"/>
            <rect x="56" y="30" width="5" height="10"/><rect x="64" y="34" width="5" height="10"/>
            <rect x="72" y="30" width="5" height="12"/><rect x="80" y="36" width="5" height="9"/>
            <rect x="88" y="32" width="5" height="11"/><rect x="96" y="30" width="5" height="11"/>
          </g>
          <text class="s-tiny" x="8" y="68">Text Text Text Text Text Text Text Text Text Text Text Text</text>
        </g>
      </defs>
      <text class="s-title" x="190" y="19" text-anchor="middle">Lorem ipsum dolor sit amet</text>
      <text class="s-sub" x="190" y="33" text-anchor="middle">Lorem ipsum dolor sit amet, consectetuer adipiscing elit. Aenean commodo ligula eget dolor.</text>
      <use href="#mini-chart" x="27" y="54"/>
      <use href="#mini-chart" x="148" y="54"/>
      <use href="#mini-chart" x="27" y="131"/>
      <use href="#mini-chart" x="148" y="131"/>
      <g class="s-tiny">
        <text x="282" y="74">• Lorem ipsum dolor sit amet,</text>
        <text x="285" y="80">consectetuer adipiscing elit, sed</text>
        <text x="285" y="86">diam nonummy eirmod tempor</text>
        <text x="285" y="92">invidunt ut labore et dolore.</text>
        <text x="285" y="118">Lorem ipsum dolor sit amet,</text>
        <text x="285" y="124">consectetuer adipiscing elit, sed</text>
        <text x="285" y="130">diam nonummy eirmod tempor</text>
        <text x="285" y="136">invidunt ut labore et dolore.</text>
        <text x="285" y="162">Lorem ipsum dolor sit amet,</text>
        <text x="285" y="168">consectetuer adipiscing elit, sed</text>
        <text x="285" y="174">diam nonummy eirmod tempor</text>
        <text x="285" y="180">invidunt ut labore et dolore.</text>
      </g>
    </svg>
  </div>

  <div class="slide slide-two">
    <svg viewBox="0 0 380 214">
      <text class="s-title" x="190" y="19" text-anchor="middle">Lorem ipsum dolor sit amet</text>
      <text class="s-sub" x="190" y="33" text-anchor="middle">Lorem ipsum dolor sit amet, consectetuer adipiscing elit. Aenean commodo ligula eget dolor.</text>
      <g class="s-tiny" style="font-size:4.4px">
        <text x="28" y="88">• Lorem ipsum dolor sit amet,</text>
        <text x="31" y="95">consectetuer adipiscing elit,</text>
        <text x="31" y="102">sed diam nonummy eirmod</text>
        <text x="31" y="109">tempor invidunt ut labore et</text>
        <text x="31" y="116">dolore magna aliquyam erat.</text>
        <text x="28" y="144">• Lorem ipsum dolor sit amet,</text>
        <text x="31" y="151">consectetuer adipiscing elit,</text>
        <text x="31" y="158">sed diam nonummy eirmod</text>
        <text x="31" y="165">tempor invidunt ut labore et</text>
        <text x="31" y="172">dolore magna aliquyam erat.</text>
      </g>
      <g fill="var(--blue)">
        <rect x="115" y="148" width="12" height="39"/><rect x="132" y="145" width="12" height="42"/>
        <rect x="149" y="136" width="12" height="51"/><rect x="166" y="124" width="12" height="63"/>
        <rect x="183" y="121" width="12" height="66"/><rect x="200" y="115" width="12" height="72"/>
        <rect x="217" y="109" width="12" height="78"/><rect x="234" y="100" width="12" height="87"/>
        <rect x="251" y="100" width="12" height="87"/><rect x="268" y="94" width="12" height="93"/>
        <rect x="285" y="91" width="12" height="96"/><rect x="302" y="85" width="12" height="102"/>
      </g>
      <g class="s-val" text-anchor="middle">
        <text x="121" y="170">13</text><text x="138" y="168">14</text><text x="155" y="164">17</text>
        <text x="172" y="157">21</text><text x="189" y="155">22</text><text x="206" y="152">24</text>
        <text x="223" y="148">26</text><text x="240" y="145">29</text><text x="257" y="145">29</text>
        <text x="274" y="142">31</text><text x="291" y="141">32</text><text x="308" y="138">34</text>
      </g>
      <polyline fill="none" stroke="#b8c0c8" stroke-width="0.8"
        points="121,135 138,132 155,122 172,109 189,106 206,99 223,93 240,83 257,83 274,76 291,70 308,70 320,70"/>
      <g fill="var(--white)" stroke="#9aa4ae" stroke-width="0.6">
        <circle cx="121" cy="135" r="1.8"/><circle cx="138" cy="132" r="1.8"/><circle cx="155" cy="122" r="1.8"/>
        <circle cx="172" cy="109" r="1.8"/><circle cx="189" cy="106" r="1.8"/><circle cx="206" cy="99" r="1.8"/>
        <circle cx="223" cy="93" r="1.8"/><circle cx="240" cy="83" r="1.8"/><circle cx="257" cy="83" r="1.8"/>
        <circle cx="274" cy="76" r="1.8"/><circle cx="291" cy="70" r="1.8"/><circle cx="308" cy="70" r="1.8"/>
      </g>
      <g class="s-lbl" text-anchor="middle">
        <text x="121" y="131">16</text><text x="138" y="128">17</text><text x="155" y="118">20</text>
        <text x="172" y="105">24</text><text x="189" y="102">25</text><text x="206" y="95">27</text>
        <text x="223" y="89">29</text><text x="240" y="79">32</text><text x="257" y="79">32</text>
        <text x="274" y="72">34</text><text x="291" y="66">36</text><text x="308" y="66">36</text>
      </g>
      <text class="s-lbl" x="320" y="78">Lorem ipsum</text>
      <text class="s-acc" x="320" y="138">Lorem ipsum</text>
      <g class="s-lbl" text-anchor="middle">
        <text x="121" y="196">Text</text><text x="138" y="196">Text</text><text x="155" y="196">Text</text>
        <text x="172" y="196">Text</text><text x="189" y="196">Text</text><text x="206" y="196">Text</text>
        <text x="223" y="196">Text</text><text x="240" y="196">Text</text><text x="257" y="196">Text</text>
        <text x="274" y="196">Text</text><text x="291" y="196">Text</text><text x="308" y="196">Text</text>
      </g>
    </svg>
  </div>

  <div class="slide slide-three">
    <svg viewBox="0 0 380 214">
      <text class="s-title" x="190" y="19" text-anchor="middle">Lorem ipsum dolor sit amet</text>
      <text class="s-sub" x="190" y="33" text-anchor="middle">Lorem ipsum dolor sit amet, consectetuer adipiscing elit. Aenean commodo ligula eget dolor.</text>
      <text class="s-cap" x="39" y="50">Lorem ipsum</text>
      <text class="s-tiny" x="39" y="57">Lorem ipsum dolor sit amet, consectetuer sadipscing elitr, sed diam nonumy eirmod tempor</text>
      <text class="s-tiny" x="39" y="62">invidunt ut labore et dolore magna aliquyam erat, sed diam voluptua. At vero eos et accusam.</text>
      <g class="s-tiny" style="font-size:4.4px">
        <text x="26" y="78">Text</text><text x="26" y="89.5">Text</text><text x="26" y="101">Text</text>
        <text x="26" y="112.5">Text</text><text x="26" y="124">Text</text><text x="26" y="135.5">Text</text>
        <text x="26" y="147">Text</text><text x="26" y="158.5">Text</text><text x="26" y="170">Text</text>
        <text x="26" y="181.5">Text</text>
      </g>
      <g fill="var(--navy)">
        <rect x="40" y="74" width="109" height="5"/><rect x="40" y="85.5" width="102" height="5"/>
        <rect x="40" y="97" width="102" height="5"/><rect x="40" y="108.5" width="88" height="5"/>
        <rect x="40" y="120" width="84" height="5"/><rect x="40" y="131.5" width="77" height="5"/>
        <rect x="40" y="143" width="74" height="5"/><rect x="40" y="154.5" width="60" height="5"/>
        <rect x="40" y="166" width="49" height="5"/><rect x="40" y="177.5" width="46" height="5"/>
      </g>
      <g class="s-lbl" style="fill:var(--ink)">
        <text x="152" y="78.5">31</text><text x="145" y="90">29</text><text x="145" y="101.5">29</text>
        <text x="131" y="113">25</text><text x="127" y="124.5">24</text><text x="120" y="136">22</text>
        <text x="117" y="147.5">21</text><text x="103" y="159">17</text><text x="92" y="170.5">14</text>
        <text x="89" y="182">13</text>
      </g>
      <g fill="var(--blue)">
        <rect x="221" y="74" width="24" height="5"/><rect x="221" y="85.5" width="32" height="5"/>
        <rect x="205" y="97" width="16" height="5"/><rect x="213" y="108.5" width="8" height="5"/>
        <rect x="221" y="120" width="24" height="5"/><rect x="221" y="131.5" width="24" height="5"/>
        <rect x="221" y="143" width="8" height="5"/><rect x="213" y="154.5" width="8" height="5"/>
        <rect x="221" y="166" width="32" height="5"/><rect x="221" y="177.5" width="16" height="5"/>
      </g>
      <g class="s-acc">
        <text x="248" y="78.5">+3%</text><text x="256" y="90">+4%</text><text x="192" y="101.5">-2%</text>
        <text x="200" y="113">-1%</text><text x="248" y="124.5">+3%</text><text x="248" y="136">+3%</text>
        <text x="232" y="147.5">+1%</text><text x="200" y="159">-1%</text><text x="256" y="170.5">+4%</text>
        <text x="240" y="182">+2%</text>
      </g>
      <g class="s-tiny">
        <text x="282" y="74">• Lorem ipsum dolor sit amet,</text>
        <text x="285" y="80">consectetuer adipiscing elit, sed</text>
        <text x="285" y="86">diam nonummy eirmod tempor</text>
        <text x="285" y="92">invidunt ut labore et dolore.</text>
        <text x="285" y="118">Lorem ipsum dolor sit amet,</text>
        <text x="285" y="124">consectetuer adipiscing elit, sed</text>
        <text x="285" y="130">diam nonummy eirmod tempor</text>
        <text x="285" y="136">invidunt ut labore et dolore.</text>
        <text x="282" y="162">• Lorem ipsum dolor sit amet,</text>
        <text x="285" y="168">consectetuer adipiscing elit, sed</text>
        <text x="285" y="174">diam nonummy eirmod tempor</text>
        <text x="285" y="180">invidunt ut labore et dolore.</text>
      </g>
    </svg>
  </div>

  <div class="headline">
    <h1 class="headline-title">Standard<br>Graphs</h1>
    <p class="headline-sub">Slide Deck Presentation 1</p>
  </div>
</div>
</body>
</html>
```